Brellwick Partners, LLC Stationary

Brellwick Partners, LLC is a new financial planning and consulting company. We are looking for designs on business cards, letterhead, envelopes, and anything else that would be useful. Our preference for business card design is two sided. We are looking for a professional and clean look with incorporating the logo and patriotic feel. Thank you to all who participate and good luck!

```html
<!DOCTYPE html>
<html lang="en">
<head>
<meta charset="utf-8">
<title>Brellwick Partners, LLC – Business Card</title>
<link rel="stylesheet" href="https://fonts.googleapis.com/css2?family=Montserrat:wght@300;400;700&display=swap">
<style>
  :root {
    --red: #c61f2e;
    --red-deep: #9e1622;
    --blue: #1f3d6b;
    --white: #ffffff;
    --ink: #3a3a3a;
    --stage: #ebe8e3;
    --pattern-pink: #f6dadd;
    --pattern-blue: #dfe5ee;
  }
  * { box-sizing: border-box; margin: 0; padding: 0; }
  html, body { width: 1200px; height: 950px; overflow: hidden; }
  body {
    background: var(--stage);
    font-family: "Montserrat", sans-serif;
    display: flex; align-items: center; justify-content: center; gap: 80px;
  }
  .card {
    position: relative; width: 380px; height: 665px;
    background: var(--white); overflow: hidden;
    box-shadow: 0 10px 30px rgba(0,0,0,.18);
  }
  .card-art { position: absolute; inset: 0; }
  .brand {
    position: absolute; top: 34px; right: 28px; text-align: right;
    color: var(--blue); font-weight: 700;
  }
  .brand-name { font-size: 30px; letter-spacing: 1px; text-transform: uppercase; line-height: 1; }
  .brand-sub { font-size: 13px; letter-spacing: 3px; text-transform: uppercase; margin-top: 6px; }
  .brand-tagline {
    font-size: 7px; font-weight: 400; letter-spacing: 1.5px; text-transform: uppercase;
    color: var(--ink); margin-top: 6px; padding-top: 4px; border-top: 1px solid var(--red);
  }
  .brand-dot {
    position: absolute; top: 40px; left: 34px; width: 22px; height: 22px;
    border-radius: 50%; background: var(--red);
  }
  .contact {
    position: absolute; left: 30px; bottom: 26px; height: 320px;
    writing-mode: vertical-rl; transform: rotate(180deg);
    color: var(--white); white-space: nowrap;
  }
  .contact-name { font-size: 19px; font-weight: 700; letter-spacing: 1px; text-transform: uppercase; line-height: 1.2; }
  .contact-role { font-size: 12px; font-weight: 300; letter-spacing: 2px; text-transform: uppercase; margin-left: 10px; line-height: 1.4; }
  .contact-line { font-size: 12.5px; font-weight: 300; line-height: 1.5; }
  .contact-line svg { width: 11px; height: 11px; margin-bottom: 6px; vertical-align: middle; }
  .back-brand {
    position: absolute; top: 50%; left: 50%; transform: translate(-50%, -50%);
    display: flex; align-items: center; gap: 10px;
    color: var(--blue); font-weight: 700; font-size: 17px; white-space: nowrap;
  }
  .back-brand .dot { width: 16px; height: 16px; border-radius: 50%; background: var(--red); }
  .web {
    position: absolute; left: 34px; top: 40px;
    transform-origin: top left; transform: rotate(90deg) translateY(-100%);
    font-size: 13px; letter-spacing: 5px; color: var(--ink); white-space: nowrap;
  }
</style>
</head>
<body>

  <section class="card card-front">
    <svg class="card-art" viewBox="0 0 380 665" preserveAspectRatio="none">
      <polygon points="0,250 380,380 380,665 0,665" fill="var(--red)"/>
      <polygon points="0,250 380,380 160,330 0,320" fill="var(--blue)"/>
      <defs>
        <linearGradient id="emblemFill" x1="0" y1="0" x2="0" y2="1">
          <stop offset="0" stop-color="#d42a38"/>
          <stop offset="1" stop-color="#a5182a"/>
        </linearGradient>
      </defs>
      <rect x="200" y="260" width="150" height="250" rx="10" fill="url(#emblemFill)"
            role="img" aria-label="Large eagle and star emblem illustration"/>
    </svg>

    <span class="brand-dot"></span>
    <div class="brand">
      <div class="brand-name">Brellwick</div>
      <div class="brand-sub">Partners, LLC</div>
      <div class="brand-tagline">Financial Planning &amp; Consulting</div>
    </div>

    <div class="contact">
      <div class="contact-name">Dana Whitfield</div>
      <div class="contact-role">CEO / Founder</div>
      <div class="contact-line">1420 Harlow Street</div>
      <div class="contact-line">Fairbanks, Alaska 34512</div>
      <div class="contact-line">
        <svg viewBox="0 0 12 12"><path d="M2 1h3l1 3-2 1a7 7 0 0 0 3 3l1-2 3 1v3c-6 0-9-3-9-9z" fill="currentColor"/></svg>
        555 210 4817
      </div>
      <div class="contact-line">
        <svg viewBox="0 0 12 12"><rect x="3" y="1" width="6" height="10" rx="1" fill="none" stroke="currentColor"/></svg>
        555 384 6091
      </div>
      <div class="contact-line">
        <svg viewBox="0 0 12 12"><rect x="1" y="3" width="10" height="7" fill="none" stroke="currentColor"/><path d="M1 3l5 4 5-4" fill="none" stroke="currentColor"/></svg>
        hello@brellwick.com
      </div>
      <div class="contact-line">
        <svg viewBox="0 0 12 12"><circle cx="6" cy="6" r="5" fill="none" stroke="currentColor"/><path d="M1 6h10M6 1c-3 3-3 7 0 10M6 1c3 3 3 7 0 10" fill="none" stroke="currentColor"/></svg>
        www.brellwick.com
      </div>
    </div>
  </section>

  <section class="card card-back">
    <svg class="card-art" viewBox="0 0 380 665" preserveAspectRatio="none"
         role="img" aria-label="Faint repeating eagle and star pattern">
      <defs>
        <linearGradient id="patternFill" x1="0" y1="0" x2="1" y2="1">
          <stop offset="0" stop-color="var(--pattern-pink)"/>
          <stop offset="0.5" stop-color="#fbf3f4"/>
          <stop offset="1" stop-color="var(--pattern-blue)"/>
        </linearGradient>
      </defs>
      <rect width="380" height="665" fill="url(#patternFill)"/>
    </svg>
    <div class="web">www.brellwick.com</div>
    <div class="back-brand"><span class="dot"></span>Brellwick Partners, LLC</div>
  </section>

</body>
</html>
```